KRT Info Brochure

We need a brochure design for a new not-for-profit organisation that is aimed at providing homeless people with a residence that also provides counselling and vocational training to assist them to find suitable employment at the end of the program.
PLEASE NOTE:
Brochure to be A4.
I know the brochure is quite long, it is really a booklet, but please note that it does not have to have a lot of work done on it, I just want it to look professional and the front cover and inside page to look good.
Also please leave about 2-3 pages at the end as I will be adding in some architect drawings.
Please add in a last page with Contact written at the bottom - we will fill that in later. So please ensure it is editable in PDF.
Thank you so much.
Cheers
Marta

```html
<!DOCTYPE html>
<html lang="en">
<head>
<meta charset="utf-8">
<title>KRT Info Brochure – Spread</title>
<link href="https://fonts.googleapis.com/css2?family=Open+Sans:wght@400;600;700&display=swap" rel="stylesheet">
<style>
  :root{
    --backdrop:#e6e6e6;
    --paper:#ffffff;
    --olive:#8c8a3c;
    --olive-dark:#6d6b2a;
    --olive-soft:#b7b57a;
    --gold:#f2a91d;
    --cream:#ebe8b0;
    --row-a:#dfe3b8;
    --row-b:#eef0d6;
    --ink:#3a3a32;
    --photo-people:linear-gradient(135deg,#cfc9c4,#6d6a6e 55%,#2f3140);
    --photo-warm:linear-gradient(135deg,#e8e4dc,#bfb3a3);
    --photo-soil:linear-gradient(135deg,#7a6f5c,#3e362b);
    --photo-plant:linear-gradient(135deg,#5d6a3a,#2c2a1e);
  }
  *{box-sizing:border-box;margin:0;padding:0}
  html,body{width:1200px;height:847px;overflow:hidden;background:var(--backdrop)}
  body{font-family:"Open Sans",Arial,sans-serif;color:var(--ink)}
  .spread{position:absolute;left:50px;top:35px;width:1100px;height:778px;display:flex;box-shadow:0 6px 24px rgba(0,0,0,.18)}
  .page{position:relative;width:550px;height:778px;background:var(--paper);overflow:hidden}
  .band{position:absolute;left:0;width:100%}
  .band--top{top:0;height:90px}
  .band--bottom{bottom:0;height:120px}
  .content{position:absolute;left:34px;right:30px}
  h2{color:var(--olive);font-size:17px;font-weight:700;line-height:1.1;margin:10px 0 3px}
  p{font-size:9.6px;line-height:1.38;margin-bottom:8px}
  .photo{position:absolute;border-radius:2px}
  .photo--team{left:60px;top:470px;width:380px;height:205px;background:var(--photo-people);border-radius:40% 40% 0 0/30% 30% 0 0}
  .photo--desk{left:34px;top:118px;width:140px;height:92px;background:var(--photo-warm)}
  .photo--hands{left:34px;top:218px;width:140px;height:90px;background:var(--photo-warm)}
  .photo--soil{left:34px;top:316px;width:140px;height:88px;background:var(--photo-soil)}
  .photo--plant{left:395px;top:470px;width:125px;height:105px;background:var(--photo-plant)}
  .staff-table{position:absolute;left:188px;top:178px;width:335px;border-collapse:separate;border-spacing:0 1px;font-size:7.4px}
  .staff-table th{background:var(--olive);color:#fff;font-weight:600;font-size:8.5px;height:13px;line-height:1}
  .staff-table .group{background:var(--cream);font-size:9.5px;text-align:center;width:88px;border-right:4px solid #fff}
  .staff-table td.role{height:10px;padding-left:8px;line-height:1}
  .staff-table tr:nth-child(odd) td.role{background:var(--row-a)}
  .staff-table tr:nth-child(even) td.role{background:var(--row-b)}
  .features{list-style:none;margin:2px 0 6px 0;width:340px}
  .features li{font-size:9.6px;line-height:1.3;padding-left:15px;position:relative}
  .features li::before{content:"";position:absolute;left:0;top:3px;width:8px;height:8px;border-radius:50%;background:var(--gold)}
</style>
</head>
<body>
<main class="spread">

  <section class="page page--left">
    <svg class="band band--top" viewBox="0 0 550 90" preserveAspectRatio="none">
      <path d="M0 0H550V22C380 62 180 74 0 64Z" fill="var(--olive)"/>
      <path d="M0 70C180 80 380 68 550 28" fill="none" stroke="var(--gold)" stroke-width="3"/>
    </svg>

    <div class="content" style="top:84px">
      <h2>3.1. Management</h2>
      <p>There will be a KRT Management Committee who will oversee the Foundation. The Management Committee will be made up of seven individuals elected bi-annually and the CEO/Founder will act as the Management Committee President. The Committee will be selected from a wide range of experienced individuals with skills ranging from law, finance and psychology.</p>

      <h2>3.2. Business Location</h2>
      <p>The initial KRT facility will be located in the Sunshine Coast Hinterland (approx. 90kms from Brisbane). This location has been chosen as Queensland, the ACT and the Northern Territory have the highest population of homeless people. Given the central location and affordability of property it has been deemed that South East Queensland is the optimal location.</p>
      <p>The facility will be located on large rural acreage that will enable the implementation of all five phases of the supplemental businesses within the Sunshine Coast tourist belt. The location is also optimal for the peace and solitude required for the Residents whilst they heal emotionally and psychologically.</p>
      <p>Furthermore, the location is ideally located to take advantage of the local job market in the Sunshine Coast and Brisbane for Residents at the completion of the Program.</p>
      <p>Residents will be accepted from all over Australia. Residents will be flown from their location to the KRT complex and returned to their original location if required. Aftercare assistance will be provided to Clients regardless of their location.</p>

      <h2>3.3. Foundation Management</h2>
      <p>Marta Lowell is the founder/Chief Executive Officer of the KRT foundation. Marta has a Bachelor of Business / Bachelor of Arts as well as extensive experience working in youth job counselling and vocational training and has 20+ years in senior management experience.</p>
    </div>

    <div class="photo photo--team" role="img" aria-label="Photo of the foundation management team in business attire"></div>

    <svg class="band band--bottom" viewBox="0 0 550 120" preserveAspectRatio="none">
      <path d="M0 60C200 40 380 30 550 8V120H0Z" fill="var(--olive)"/>
      <path d="M300 34C380 26 470 18 550 8V120H300Z" fill="var(--olive-soft)"/>
      <path d="M0 54C200 34 380 24 550 2" fill="none" stroke="var(--gold)" stroke-width="3"/>
    </svg>
  </section>

  <section class="page page--right">
    <svg class="band band--top" viewBox="0 0 550 90" preserveAspectRatio="none">
      <path d="M0 0H550V34C400 22 200 14 0 30Z" fill="var(--olive)"/>
      <path d="M0 0H170V22C110 26 60 28 0 30Z" fill="var(--olive-soft)"/>
      <path d="M0 36C200 20 400 28 550 40" fill="none" stroke="var(--gold)" stroke-width="3"/>
    </svg>

    <div class="content" style="top:38px;left:188px">
      <h2>3.4. KRT Staff</h2>
      <p>It is expected that KRT will employ 17 staff (in addition to the CEO), including 4 onsite staff. It is expected that a full contingent of staff will not be required until the facility reaches full capacity. In addition to specialist staff, KRT will seek the services of volunteers to assist with training and medical requirements (eg. Chiropractor, massage therapist etc).</p>
    </div>

    <div class="photo photo--desk" role="img" aria-label="Photo of a counselling session at a desk"></div>
    <div class="photo photo--hands" role="img" aria-label="Photo of hands stacking coins on a table"></div>
    <div class="photo photo--soil" role="img" aria-label="Photo of a person standing on dark soil"></div>

    <table class="staff-table">
      <tr><th colspan="2">Staff Requirements</th></tr>
      <tr><td class="group" rowspan="5">Counselling Staff</td><td class="role">Senior Psychologist</td></tr>
      <tr><td class="role">Psychologist x 2</td></tr>
      <tr><td class="role">Counsellors x 2</td></tr>
      <tr><td class="role">Residential Mentor x 2 (onsite)</td></tr>
      <tr><td class="role">Case Workers x 2</td></tr>
      <tr><td class="group" rowspan="9">Admin Staff</td><td class="role">Operations Manager</td></tr>
      <tr><td class="role">Personal Assistant</td></tr>
      <tr><td class="role">Information Technology Manager/Trainer</td></tr>
      <tr><td class="role">H.R. Manager</td></tr>
      <tr><td class="role">Marketing/Promotions Manager</td></tr>
      <tr><td class="role">Office Manager</td></tr>
      <tr><td class="role">Administration Assistant x 2</td></tr>
      <tr><td class="role">Training Co-ordinator</td></tr>
      <tr><td class="role">Book Keeper (Part time)</td></tr>
      <tr><td class="group" rowspan="5">General Staff</td><td class="role">Cooks x 2</td></tr>
      <tr><td class="role">Barista</td></tr>
      <tr><td class="role">Grounds Person x 2</td></tr>
      <tr><td class="role">Facility Supervisor (onsite)</td></tr>
      <tr><td class="role">Night guard (onsite)</td></tr>
    </table>

    <div class="content" style="top:418px">
      <h2>3.5. Self-Sustainment</h2>
      <p style="width:350px">As previously mentioned, KRT aims to be as self-sustaining as possible in an attempt to reduce the environmental footprint of KRT and the on-going costs. Below is a list of some of the environmentally friendly / self-sustaining options KRT plans to implement. These self-sustaining options will also be used in the complementary businesses through publications and workshops.</p>
      <ul class="features">
        <li>Solar and wind power</li>
        <li>Rainwater tanks</li>
        <li>Environmentally friendly insulation</li>
        <li>Grey water tanks</li>
        <li>Sewerage - worm farm waste system</li>
        <li>Organic fruit, vegetable and flower farm</li>
        <li>Fish farm system</li>
        <li>Chicken coop recycling/compost</li>
      </ul>
      <p style="width:330px">The long-term aim is to bring tourist to the site, using the self-sustaining aspect of the compex, where there will be an on-site coffee shop and gallery; we believe that the self-sustainment project may also interest the environmental sector.</p>
    </div>

    <div class="photo photo--plant" role="img" aria-label="Photo of cupped hands holding soil with a young seedling"></div>

    <svg class="band band--bottom" viewBox="0 0 550 120" preserveAspectRatio="none">
      <path d="M0 50C180 58 380 66 550 70V120H0Z" fill="var(--olive)"/>
      <path d="M0 44C180 52 380 60 550 64" fill="none" stroke="var(--gold)" stroke-width="3"/>
    </svg>
  </section>

</main>
</body>
</html>
```